Letter design, envelope design, and more

Hello, we the Tavrin Gmbh are looking for our shop. Letter C5. Design does not have to be like a business card, so it can have straight lines. Only the color is important. The logo is the text under TaVRin omit.It should not be playful but Profesionel

Font styles to use
Sans Serif

Colors
0555a3
3176b5
85abd2
85cae6
34a7d8
0792cd
cee9f5
cfdfed
000000

Requirements
Must have
• Color like business card, Please, with the text under TaVRin, Correct address Lindmattstr. 4 Zip code 9517 Brennwil, as well as Couvert Without addressing only design and logo with TaVrn
Nice to have
• more writing articles
Should not have
• Not too colored, Text under TaVRin, bright colors

```html
<!DOCTYPE html>
<html lang="en">
<head>
<meta charset="utf-8">
<title>Tavrin GmbH – Stationery</title>
<link href="https://fonts.googleapis.com/css2?family=Lato:wght@400;700&family=Kaushan+Script&display=swap" rel="stylesheet">
<style>
:root{
  --navy:#242466;
  --flap:#37356e;
  --steel:#7e97b3;
  --ink:#3a3a3a;
  --paper:#ffffff;
  --stage:#e1e2e4;
  --edge:#c9c9cc;
}
*{margin:0;padding:0;box-sizing:border-box}
html,body{width:1200px;height:641px;overflow:hidden;background:var(--stage);font-family:'Lato',sans-serif}
.canvas{position:relative;width:1200px;height:641px}

/* letter */
.letter{position:absolute;left:76px;top:64px;width:363px;height:512px;background:var(--paper);border:1px solid var(--edge)}
.brand{position:absolute;display:flex;align-items:center;gap:6px;color:var(--navy);font-weight:700;letter-spacing:1px}
.brand .mark{display:block;background:var(--navy)}
.letter .brand{left:21px;top:20px;font-size:19px}
.letter .brand .mark{width:16px;height:16px}
.contact{position:absolute;left:278px;top:14px;border-left:1px solid #cfcfd4;padding-left:6px;font-size:6.6px;line-height:11px;color:var(--ink)}
.contact li{list-style:none;display:flex;align-items:center;gap:3px}
.contact svg{width:6px;height:6px}
.salutation{position:absolute;left:20px;top:86px;font-size:9px;font-weight:700;color:var(--navy)}
.body-copy{position:absolute;left:20px;top:104px;width:327px;font-size:6.5px;font-weight:400;line-height:11px;color:var(--ink);text-align:justify}
.body-copy p{margin-bottom:8.6px}
.closing{position:absolute;left:20px;top:396px;font-size:11px;color:var(--ink)}
.signature{position:absolute;left:20px;top:413px;font-family:'Kaushan Script',cursive;font-size:15px;color:var(--navy)}
.letter-foot{position:absolute;left:0;right:0;top:478px;height:30px}
.band-line{position:absolute;left:0;right:0;height:1.5px;background:var(--navy)}
.band{position:absolute;left:0;height:18px;background:var(--navy);color:#fff;display:flex;align-items:center;gap:4px;padding-left:16px;font-size:6.6px}
.foot-square{position:absolute;width:20px;height:20px;background:var(--navy)}

/* envelopes */
.envelope{position:absolute;background:var(--paper);border:1px solid var(--edge);overflow:hidden}
.env-back{left:606px;top:98px;width:540px;height:242px}
.env-mid{left:566px;top:202px;width:540px;height:241px}
.env-front{left:476px;top:309px;width:541px;height:242px}
.flap{position:absolute;left:0;top:0;width:100%}
.flap-name{position:absolute;left:0;right:0;text-align:center;font-weight:700;letter-spacing:2px;font-size:18px}
.env-back .flap-name{top:28px;color:#fff}
.env-mid .flap-name{top:32px;color:var(--navy)}
.env-front .brand{left:18px;top:22px;font-size:22px}
.env-front .brand .mark{width:20px;height:20px}
.return-address{position:absolute;left:18px;top:64px;display:flex;align-items:center;gap:4px;font-size:9px;color:#222}
.env-foot{position:absolute;left:0;right:0;top:207px;height:24px}
.env-foot .band{height:18px;top:3px;width:482px;padding-left:15px;font-size:9.5px;letter-spacing:2px}
</style>
</head>
<body>
<div class="canvas">

  <section class="letter">
    <div class="brand"><span class="mark"></span>TAVRIN</div>
    <ul class="contact">
      <li><svg viewBox="0 0 10 10"><circle cx="5" cy="5" r="4.3" fill="none" stroke="#242466"/><path d="M3.5 3c.3 2 1.5 3.3 3.3 3.6" stroke="#242466" fill="none"/></svg>+41 71 555 02 18</li>
      <li><svg viewBox="0 0 10 10"><rect x="1" y="2.5" width="8" height="5" fill="#242466"/><path d="M1 2.5l4 3 4-3" stroke="#fff" fill="none" stroke-width=".8"/></svg>info@tavrin.ch</li>
      <li><svg viewBox="0 0 10 10"><circle cx="5" cy="5" r="4.2" fill="none" stroke="#242466"/><path d="M1 5h8M5 1c-2 2.5-2 5.5 0 8M5 1c2 2.5 2 5.5 0 8" stroke="#242466" fill="none" stroke-width=".7"/></svg>www.tavrin.ch</li>
    </ul>
    <h1 class="salutation">Dear Mr. Lorem,</h1>
    <div class="body-copy">
      <p>Lorem ipsum dolor sit amet, consectetuer adipiscing elit, sed diam nonummy nibh euismod tincidunt ut laoreet dolore magna aliquam erat volutpat. Ut wisi enim ad minim veniam, quis nostrud exerci tation ullamcorper suscipit lobortis nisl ut aliquip ex ea commodo consequat. Duis autem vel eum iriure dolor in hendiusto odio dignissim qui blandit praesent luptatum zzril delenit.facilisi.</p>
      <p>Lorem ipsum dolor sit amet, consectetuer adipiscing elit, sed diam nonummy nibh euismod tincidunt ut laoreet dolore magna aliquam erat volutpat. Ut wisi enim ad minim veniam, quis nostrud exerci tation ullamcorper suscipit lobortis nisl ut aliquip ex ea commodo consequat.</p>
      <p>Lorem ipsum dolor sit amet, consectetuer adipiscing elit, sed diam nonummy nibh euismod tincidunt ut laoreet dolore magna aliquam erat volutpat. Ut wisi enim ad minim veniam, quis nostrud exerci tation ullamcorper suscipit lobortis nisl ut aliquip ex ea commodo consequat. Duis autem vel eum iriure dolor in hendiusto odio dignissim qui blandit praesent luptatum zzril delenit.facilisi.</p>
      <p>Lorem ipsum dolor sit amet, consectetuer adipiscing elit, sed diam nonummy nibh euismod tincidunt ut laoreet dolore magna aliquam erat volutpat. Ut wisi enim ad minim veniam, quis nostrud exerci tation ullamcorper suscipit lobortis nisl ut aliquip ex ea commodo consequat.</p>
      <p>Lorem ipsum dolor sit amet, consectetuer adipiscing elit, sed diam nonummy nibh euismod tincidunt ut laoreet dolore magna aliquam erat volutpat. Ut wisi enim ad minim veniam, quis nostrud exerci tation ullamcorper suscipit lobortis nisl ut aliquip ex ea commodo consequat. Duis autem vel eum iriure dolor in hendiusto odio dignissim qui blandit praesent luptatum zzril delenit.facilisi.</p>
      <p>Lorem ipsum dolor sit amet, consectetuer adipiscing elit, sed diam nonummy nibh euismod tincidunt ut laoreet dolore magna aliquam erat volutpat. Ut wisi enim ad minim veniam, quis nostrud exerci tation ullamcorper suscipit lobortis nisl ut aliquip ex ea commodo consequat.</p>
    </div>
    <p class="closing">Sincerely Your,</p>
    <p class="signature">Your Name</p>
    <div class="letter-foot">
      <span class="band-line" style="top:0"></span>
      <div class="band" style="top:4px;width:308px">
        <svg viewBox="0 0 10 10" width="6" height="6"><circle cx="5" cy="5" r="4.3" fill="none" stroke="#fff"/><circle cx="5" cy="4.3" r="1.4" fill="#fff"/></svg>
        Lindmattstr. 4, Zip code 9517 Brennwil
      </div>
      <span class="band-line" style="top:28px"></span>
      <span class="foot-square" style="left:316px;top:4px"></span>
    </div>
  </section>

  <section class="envelope env-back">
    <svg class="flap" viewBox="0 0 540 100" height="100" preserveAspectRatio="none">
      <path d="M0 0H540V0c-6 26-20 40-60 48L280 93c-6 2-14 2-20 0L60 48C20 40 6 26 0 0Z" fill="#37356e"/>
    </svg>
    <div class="flap-name">TAVRIN</div>
  </section>

  <section class="envelope env-mid">
    <svg class="flap" viewBox="0 0 540 96" height="96" preserveAspectRatio="none">
      <path d="M0 0c6 28 16 44 50 52L255 92c6 2 14 2 20 0L490 52c34-8 44-24 50-52" fill="none" stroke="#c9c9cc" stroke-width="1"/>
    </svg>
    <div class="flap-name">TAVRIN</div>
  </section>

  <section class="envelope env-front">
    <div class="brand"><span class="mark"></span>TAVRIN</div>
    <p class="return-address">
      <svg viewBox="0 0 10 10" width="8" height="8"><circle cx="5" cy="5" r="4.3" fill="none" stroke="#242466"/><circle cx="5" cy="4.3" r="1.4" fill="#242466"/></svg>
      Lindmattstr. 4, Zip code 9517 Brennwil
    </p>
    <div class="env-foot">
      <span class="band-line" style="top:0"></span>
      <div class="band">www.tavrin.ch</div>
      <span class="band-line" style="top:23px"></span>
      <span class="foot-square" style="left:488px;top:0;width:34px;height:24px"></span>
    </div>
  </section>

</div>
</body>
</html>
```